Spring Detox sale graphics for social media

You MUST read the Brief in the WORD document and follow the instructions there. I want to create 10 social media graphics (new Instagram size 4:5 (1080 x 1350 pixels) focusing on our Mother’s Day Spring Detox Sale graphics, using any of the pics attached. Use the attached pics, NO RANDOM STOCK PHOTOGRAPHY. For the color scheme of the graphics, they should all be complementary to the product colors or feel like Spring time.

Target Market(s)

primarily women

Requirements
Must have
• the photos and text attached

```html
<!DOCTYPE html>
<html lang="en">
<head>
<meta charset="utf-8">
<title>Mother's Day Spring Detox Sale – Social Set</title>
<link rel="stylesheet" href="https://fonts.googleapis.com/css2?family=Antonio:wght@700&display=swap">
<style>
:root{
  --page:#efeff0;
  --white:#ffffff;
  --magenta:#b0478f;
  --orchid:#c45fa2;
  --pink-soft:#e9b6d6;
  --blue:#2d4ea2;
  --blue-mid:#4262b4;
  --blue-soft:#c9d2ee;
  --sage:#4b6a57;
  --sage-soft:#c9d1cb;
  --plum:#7c4f8f;
  --lilac:#e6c9ee;
  --photo-light:#ece8ea;
  --photo-mid:#d6d0d3;
  --photo-dark:#3a2e30;
}
*{margin:0;padding:0;box-sizing:border-box}
html,body{width:1200px;height:1130px;overflow:hidden;background:var(--page)}
body{position:relative;font-family:"Antonio","Oswald",sans-serif;font-weight:700}
.tile{position:absolute;width:259px;height:324px;overflow:hidden;background:var(--white)}
.line{position:absolute;z-index:2;line-height:1;white-space:nowrap;text-transform:uppercase}
.left{left:9px}
.center{left:0;right:0;text-align:center}
.outline{color:transparent !important;-webkit-text-stroke-width:1.3px}
.stroke-white{-webkit-text-stroke-color:var(--white)}
.stroke-blue{-webkit-text-stroke-color:var(--blue)}
.stroke-pink{-webkit-text-stroke-color:var(--magenta)}
.t-white{color:var(--white)}
.t-blue{color:var(--blue)}
.t-bluemid{color:var(--blue-mid)}
.t-magenta{color:var(--magenta)}
.t-orchid{color:var(--orchid)}
.photo-person{position:absolute;z-index:1;background:linear-gradient(180deg,var(--photo-dark) 0%,var(--photo-mid) 30%,var(--photo-light) 55%,var(--photo-dark) 100%);border-radius:40px 40px 0 0;opacity:.9}
.photo-products{position:absolute;z-index:1;background:linear-gradient(180deg,var(--photo-light),var(--photo-mid));border-radius:6px}
.frame{position:absolute;z-index:0;left:17px;top:19px;width:224px;height:216px;border:1px solid var(--white);border-top:none}
.frame::before,.frame::after{content:"";position:absolute;top:0;width:25px;border-top:1px solid var(--white)}
.frame::before{left:0}
.frame::after{right:0}

.sale-magenta{left:41px;top:46px;background:linear-gradient(90deg,var(--magenta) 0%,#c77fb4 55%,var(--pink-soft) 100%)}
.sale-blue{left:327px;top:46px;background:linear-gradient(90deg,var(--blue) 0%,var(--blue-mid) 45%,var(--blue-soft) 100%)}
.sale-sage{left:614px;top:46px;background:linear-gradient(90deg,var(--sage) 0%,#7e9487 55%,var(--sage-soft) 100%)}
.sale-type-blue{left:900px;top:46px}
.sale-framed-plum{left:41px;top:403px;background:linear-gradient(180deg,var(--plum) 0%,#a57bb6 50%,var(--white) 100%)}
.sale-bottles-white{left:327px;top:403px}
.sale-plum{left:614px;top:403px;background:linear-gradient(90deg,var(--plum) 0%,#9f6fb0 50%,var(--lilac) 100%)}
.sale-framed-blue{left:900px;top:403px;background:linear-gradient(180deg,var(--blue) 0%,var(--blue-mid) 50%,var(--white) 100%)}
.sale-bottles-pink{left:327px;top:761px}
.sale-type-pink{left:614px;top:761px}
</style>
</head>
<body>

<section class="tile sale-magenta">
  <div class="photo-person" style="left:124px;top:6px;width:135px;height:240px" role="img" aria-label="Photo of a smiling woman in a white cropped sweater"></div>
  <div class="photo-products" style="left:57px;top:248px;width:202px;height:76px" role="img" aria-label="Photo of the supplement bottles and cream tubes lined up"></div>
  <div class="line t-white" style="left:13px;top:16px;font-size:21px">Mother’s Day</div>
  <div class="line t-white" style="left:13px;top:40px;font-size:39px">Spring</div>
  <div class="line t-white" style="left:13px;top:80px;font-size:43px">Detox</div>
  <div class="line outline stroke-white" style="left:13px;top:124px;font-size:63px">Sale</div>
  <div class="line t-white" style="left:13px;top:188px;font-size:29px">25% Off</div>
  <div class="line t-white" style="left:13px;top:221px;font-size:23px">Everything!</div>
</section>

<section class="tile sale-blue">
  <div class="photo-person" style="left:112px;top:8px;width:147px;height:230px" role="img" aria-label="Photo of a smiling woman holding a supplement bottle"></div>
  <div class="photo-products" style="left:22px;top:238px;width:237px;height:80px" role="img" aria-label="Photo of the supplement bottles and cream tubes lined up"></div>
  <div class="line left t-white" style="top:24px;font-size:37px">25% Off</div>
  <div class="line left t-white" style="top:62px;font-size:24px">Mother’s Day</div>
  <div class="line left t-white" style="top:88px;font-size:35px">Spring</div>
  <div class="line left t-white" style="top:121px;font-size:36px">Detox</div>
  <div class="line left outline stroke-white" style="top:157px;font-size:56px">Sale</div>
</section>

<section class="tile sale-sage">
  <div class="photo-person" style="left:112px;top:6px;width:147px;height:240px" role="img" aria-label="Photo of a smiling woman in a white cropped sweater"></div>
  <div class="photo-products" style="left:56px;top:246px;width:203px;height:76px" role="img" aria-label="Photo of the supplement bottles and cream tubes lined up"></div>
  <div class="line left t-white" style="top:33px;font-size:35px">25% Off</div>
  <div class="line left t-white" style="top:70px;font-size:17px">All Supplements</div>
  <div class="line left t-white" style="top:90px;font-size:37px">Spring</div>
  <div class="line left t-white" style="top:130px;font-size:39px">Detox</div>
  <div class="line left outline stroke-white" style="top:169px;font-size:55px">Sale!</div>
</section>

<section class="tile sale-type-blue">
  <div class="line center t-blue" style="top:31px;font-size:64px">25% Off</div>
  <div class="line center t-magenta" style="top:94px;font-size:40px">Mother’s Day</div>
  <div class="line center outline stroke-blue" style="top:129px;font-size:92px">Sale</div>
  <div class="line center t-magenta" style="top:220px;font-size:30px">Spring Detox for a</div>
  <div class="line center t-blue" style="top:251px;font-size:43px">Summer Body</div>
</section>

<section class="tile sale-framed-plum">
  <div class="frame"></div>
  <div class="line center t-white" style="top:6px;font-size:52px">25% Off</div>
  <div class="line center t-white" style="top:57px;font-size:30px">Everything</div>
  <div class="line center t-white" style="top:91px;font-size:37px">Mother’s Day</div>
  <div class="line center t-white" style="top:131px;font-size:29px">Spring Detox</div>
  <div class="line center outline stroke-white" style="top:156px;font-size:66px">Sale</div>
  <div class="photo-products" style="left:13px;top:228px;width:233px;height:90px" role="img" aria-label="Photo of four supplement bottles in a row"></div>
</section>

<section class="tile sale-bottles-white">
  <div class="photo-products" style="left:2px;top:89px;width:48px;height:78px;transform:rotate(-12deg)" role="img" aria-label="Photo of a tilted supplement bottle"></div>
  <div class="photo-products" style="left:203px;top:92px;width:55px;height:96px;transform:rotate(14deg)" role="img" aria-label="Photo of a tilted supplement bottle"></div>
  <div class="line center t-blue" style="top:14px;font-size:52px">25% Off</div>
  <div class="line center t-bluemid" style="top:68px;font-size:30px">Mother’s Day</div>
  <div class="line center outline stroke-blue" style="top:98px;font-size:61px">Sale</div>
  <div class="line center t-bluemid" style="top:160px;font-size:32px">Feel Amazing</div>
  <div class="line center t-bluemid" style="top:192px;font-size:29px">Again!</div>
  <div class="photo-products" style="left:14px;top:228px;width:232px;height:90px" role="img" aria-label="Photo of four supplement bottles in a row"></div>
</section>

<section class="tile sale-plum">
  <div class="photo-person" style="left:118px;top:10px;width:141px;height:228px" role="img" aria-label="Photo of a smiling woman holding a supplement bottle"></div>
  <div class="photo-products" style="left:20px;top:240px;width:239px;height:81px" role="img" aria-label="Photo of the supplement bottles and cream tubes lined up"></div>
  <div class="line left t-white" style="top:21px;font-size:37px">25% Off</div>
  <div class="line left t-white" style="top:60px;font-size:23px">Mother’s Day</div>
  <div class="line left outline stroke-white" style="top:84px;font-size:60px">Sale</div>
  <div class="line left t-white" style="top:145px;font-size:35px">Refresh</div>
  <div class="line left t-white" style="top:181px;font-size:36px">Your Body</div>
</section>

<section class="tile sale-framed-blue">
  <div class="frame"></div>
  <div class="line center t-white" style="top:5px;font-size:49px">25% Off</div>
  <div class="line center t-white" style="top:51px;font-size:28px">Spring Detox</div>
  <div class="line center outline stroke-white" style="top:77px;font-size:60px">Sale</div>
  <div class="line center t-white" style="top:135px;font-size:25px">Spring Cleanse.</div>
  <div class="line center t-white" style="top:161px;font-size:36px">Summer Glow</div>
  <div class="photo-products" style="left:26px;top:208px;width:208px;height:112px" role="img" aria-label="Photo of four supplement bottles grouped together"></div>
</section>

<section class="tile sale-bottles-pink">
  <div class="line center t-magenta" style="top:13px;font-size:44px">25% Off</div>
  <div class="line center t-orchid" style="top:56px;font-size:26px">Mother’s Day</div>
  <div class="line center outline stroke-pink" style="top:81px;font-size:60px">Sale</div>
  <div class="line center t-orchid" style="top:141px;font-size:23px">Detox this Spring.</div>
  <div class="line center t-magenta" style="top:165px;font-size:29px">Shine this Summer</div>
  <div class="photo-products" style="left:26px;top:204px;width:205px;height:115px" role="img" aria-label="Photo of four supplement bottles grouped together"></div>
</section>

<section class="tile sale-type-pink">
  <div class="line center t-magenta" style="top:29px;font-size:60px">25% Off</div>
  <div class="line center t-blue" style="top:87px;font-size:38px">Spring Detox</div>
  <div class="line center outline stroke-pink" style="top:127px;font-size:85px">Sale</div>
  <div class="line center t-blue" style="top:216px;font-size:36px">Spring Reset.</div>
  <div class="line center t-magenta" style="top:250px;font-size:42px">Summer Ready</div>
</section>

</body>
</html>
```